Vantiqo custom business card design

Need a authentic, innovative business card design for a new mobile app business. I am uploading a few screen images from our app for you to view. I would like app design theme to match business card design. I can also send logo images.

```html
<!DOCTYPE html>
<html lang="en">
<head>
<meta charset="utf-8">
<title>Vantiqo Business Card</title>
<link href="https://fonts.googleapis.com/css2?family=Arimo:wght@400;700&display=swap" rel="stylesheet">
<style>
  :root {
    --backdrop: #2a2a2c;
    --card-top: #1c1c1d;
    --card-bottom: #0d0d0e;
    --violet: #6a0fa8;
    --white: #f2f2f2;
    --muted: #d9d9d9;
    --rule: #5a5a5a;
  }
  * { margin: 0; padding: 0; box-sizing: border-box; }
  html, body {
    width: 1200px; height: 900px; overflow: hidden;
    background: var(--backdrop);
    font-family: "Arimo", Arial, sans-serif;
  }
  .stage {
    width: 1200px; height: 900px;
    display: flex; flex-direction: column; align-items: center; justify-content: center;
    gap: 40px;
  }
  .card {
    position: relative;
    width: 700px; height: 400px;
    background: linear-gradient(160deg, var(--card-top), var(--card-bottom));
    overflow: hidden;
  }
  .card__band {
    position: absolute; left: 0; right: 0; bottom: 0;
    height: 14px; background: var(--violet);
  }
  /* Front */
  .brand {
    position: absolute; left: 0; right: 0; top: 95px;
    display: flex; flex-direction: column; align-items: center; gap: 22px;
  }
  .brand__dot {
    width: 120px; height: 120px; border-radius: 50%;
    background: var(--violet);
  }
  .brand__name {
    color: var(--white); font-weight: 700; font-size: 54px; letter-spacing: 0.5px;
  }
  /* Back */
  .person {
    position: absolute; right: 372px; top: 150px; text-align: left;
  }
  .person__name {
    color: var(--violet); font-weight: 700; font-size: 21px; letter-spacing: 0.5px;
  }
  .person__role {
    color: var(--muted); font-size: 17px; margin-top: 2px;
  }
  .divider {
    position: absolute; left: 348px; top: 140px;
    width: 1px; height: 105px; background: var(--rule);
  }
  .contacts {
    position: absolute; left: 368px; top: 150px;
    list-style: none;
  }
  .contacts li {
    display: flex; align-items: center; gap: 10px;
    color: var(--muted); font-size: 17px; line-height: 23px; white-space: nowrap;
  }
  .contacts svg { width: 13px; height: 13px; fill: var(--violet); flex: none; }
  .address {
    position: absolute; left: 0; right: 0; top: 290px;
    text-align center; text-align: center; color: var(--white); font-size: 18px;
  }
</style>
</head>
<body>
<main class="stage">
  <section class="card card--front">
    <div class="brand">
      <div class="brand__dot"></div>
      <div class="brand__name">Vantiqo</div>
    </div>
    <div class="card__band"></div>
  </section>

  <section class="card card--back">
    <div class="person">
      <div class="person__name">MAREN HOLT</div>
      <div class="person__role">Managing Director</div>
    </div>
    <div class="divider"></div>
    <ul class="contacts">
      <li>
        <svg viewBox="0 0 16 16" aria-hidden="true"><path d="M3 1h3l1.5 4-2 1.5a9 9 0 0 0 4 4L11 8.5l4 1.5v3a2 2 0 0 1-2 2A12 12 0 0 1 1 3a2 2 0 0 1 2-2z"/></svg>
        044-310 552 847
      </li>
      <li>
        <svg viewBox="0 0 16 16" aria-hidden="true"><path d="M4 0h8a1 1 0 0 1 1 1v14a1 1 0 0 1-1 1H4a1 1 0 0 1-1-1V1a1 1 0 0 1 1-1zm1 2v10h6V2zm3 11a1 1 0 1 0 0 2 1 1 0 0 0 0-2z"/></svg>
        044-310 552 863
      </li>
      <li>
        <svg viewBox="0 0 16 16" aria-hidden="true"><path d="M0 3h16v10H0zm1.5 1.2L8 9l6.5-4.8V4h-13z"/></svg>
        hello@vantiqo.app
      </li>
      <li>
        <svg viewBox="0 0 16 16" aria-hidden="true"><circle cx="8" cy="8" r="8"/></svg>
        www.vantiqo.app
      </li>
    </ul>
    <p class="address">48 Larkfield Row, Elmbridge, Norvania, 204517.</p>
    <div class="card__band"></div>
  </section>
</main>
</body>
</html>
```